Fabrication and machining company needing printed material designs.

Heron Vessels, Inc. wants to use appealing visuals as well as informative text to tell potential clients about our capabilities in fabrication and machining. We have a new logo to showcase as well as a new website. The use of print media will allow us to leave tangible information with clients, and therefore the design will need to be concise, informative, and visually appealing.

Full Page Flyer (approx. 8.5" x 11"), front and back design. This will be a detailed offering of capabilities and services for our shop.

Half Page Flyer (approx. 5.5" x 8.5"), front and back design. An abbreviated version of the full page flyer, meant to be easily handed out and stored inside a note book.

Bi-fold business card front and back. General offerings of our services. Minimal if any details. Finished size is twice the size of a business card (approx. 4" x 3.5"), once folded in half will be the same size as a standard business card (approx. 2" x 3.5").

Please use www.heronvesselsinc.example for theme ideas. The font used for our logo is ethnocentric, not to be used for all text.

Target Market(s)

Industrial Consumers

Font styles to use
Sans Serif

```html
<!DOCTYPE html>
<html lang="en">
<head>
<meta charset="utf-8">
<title>Heron Vessels, Inc. — Flyers</title>
<link href="https://fonts.googleapis.com/css2?family=Orbitron:wght@700;800;900&family=Poppins:wght@400;500;600;700&display=swap" rel="stylesheet">
<style>
:root{
  --orange:#f47c20;
  --orange-deep:#e8692a;
  --orange-cell:#e96f34;
  --dark:#2b2b2b;
  --darker:#222222;
  --white:#ffffff;
  --ink:#222222;
  --backdrop:#7b7b7b;
  --grey-photo-a:#5c5c5c;
  --grey-photo-b:#a9a9a9;
}
*{box-sizing:border-box;margin:0;padding:0}
html,body{width:1200px;height:803px;overflow:hidden}
body{background:var(--backdrop);font-family:"Poppins",sans-serif;position:relative}
.flyer{position:absolute;top:60px;width:501px;height:648px;background:var(--white);overflow:hidden;box-shadow:0 10px 24px rgba(0,0,0,.35)}
.flyer--front{left:78px}
.flyer--back{left:632px}
.header-photo{position:absolute;left:0;top:0;width:501px;height:120px;background:linear-gradient(180deg,var(--grey-photo-a),var(--grey-photo-b) 70%,#8a8a8a)}
.brand{position:absolute;left:0;width:501px;top:26px;display:flex;flex-direction:column;align-items:center;gap:6px}
.brand__mark{width:34px;height:34px;background:var(--orange)}
.brand__name{font-family:"Orbitron",sans-serif;font-weight:800;font-size:13px;color:var(--orange);letter-spacing:.5px}
.banner{position:absolute;left:10px;top:99px;width:480px;height:43px}
.banner svg{position:absolute;inset:0}
.banner__title{position:absolute;inset:0;display:flex;align-items:center;justify-content:center;font-family:"Orbitron",sans-serif;font-weight:900;font-size:15.5px;color:var(--white);letter-spacing:.8px}
.standard{position:absolute;top:146px;left:0;width:501px;text-align:center;font-weight:600;font-size:20.5px;color:var(--ink)}
.grid{position:absolute;top:180px;left:0;width:501px;height:219px;background:var(--dark)}
.cell{position:absolute;width:120px;height:98px;display:flex;flex-direction:column;align-items:center;justify-content:flex-end;padding-bottom:14px;text-align:center}
.cell--orange{background:var(--orange-cell)}
.cell svg{margin-bottom:7px}
.cell__title{font-weight:700;font-size:9px;line-height:1.25;color:var(--orange)}
.cell--orange .cell__title{color:var(--white)}
.cell__detail{font-size:7.8px;line-height:1.25;color:var(--white)}
.services{position:absolute;top:399px;left:0;width:501px;height:193px;background:linear-gradient(180deg,#ececec,#fff 40%)}
.service{position:absolute;display:flex;gap:5px}
.service__badge{flex:none;width:21px;height:21px;border-radius:50%;border:2px solid var(--orange);background:var(--white);color:var(--orange);font-weight:700;font-size:11px;display:flex;align-items:center;justify-content:center;box-shadow:0 1px 2px rgba(0,0,0,.2)}
.service__title{font-weight:600;font-size:9.3px;color:var(--orange);line-height:1.2;margin-top:3px}
.service__list{list-style:none;font-size:8px;line-height:1.25;color:var(--ink);margin-top:2px}
.footer{position:absolute;left:0;top:592px;width:501px;height:56px;background:var(--orange-deep)}
.contacts{position:absolute;top:7px;left:10px;right:8px;display:flex;justify-content:space-between;align-items:center}
.contact{display:flex;align-items:center;gap:6px;color:var(--white);font-size:10.5px}
.contact__icon{width:18px;height:18px;border-radius:50%;background:var(--white);display:flex;align-items:center;justify-content:center}
.footer__tab{position:absolute;left:135px;top:34px;width:230px;height:22px}
.footer__tab svg{position:absolute;inset:0}
.footer__tab span{position:absolute;inset:0;display:flex;align-items:center;justify-content:center;font-size:9px;color:var(--white)}
.intro{position:absolute;top:148px;left:20px;width:461px;text-align:center;font-size:10.2px;line-height:1.25;color:var(--ink)}
.panel{position:absolute;top:180px;left:0;width:501px;height:205px;background:var(--dark)}
.sectors{position:absolute;top:1px;left:49px;width:400px;height:25px}
.sectors svg{position:absolute;inset:0}
.sectors ul{position:absolute;inset:0;list-style:none;display:flex;justify-content:space-around;align-items:center;padding:0 8px;font-weight:600;font-size:9.8px;color:var(--white)}
.offer{position:absolute;width:160px;margin-left:-80px;text-align:center;color:var(--white);font-weight:700;font-size:11.5px}
.offer svg{display:block;margin:0 auto 10px}
.gallery{position:absolute;top:385px;left:0;width:501px;height:200px;background:var(--orange-deep)}
.photo{position:absolute;top:6px;height:186px;width:159px}
.photo--welder{left:5px;background:linear-gradient(135deg,#d9781f,#3b3f66 60%,#2a2a3c)}
.photo--fittings{left:170px;background:radial-gradient(circle at 50% 45%,#e9e9e9,#9d9d9d 75%)}
.photo--pipes{left:336px;background:linear-gradient(135deg,#c9c2b1,#a7a49a 60%,#d8d3c4)}
.flyer--back .footer{top:585px;height:63px;border-top:6px solid var(--darker)}
.flyer--back .footer__tab{top:41px}
</style>
</head>
<body>

<!-- FRONT -->
<section class="flyer flyer--front">
  <div class="header-photo" role="img" aria-label="Greyscale photo of a tank fabrication yard with pipework and valves"></div>
  <div class="brand"><span class="brand__mark"></span><span class="brand__name">HERON VESSELS, INC.</span></div>
  <div class="banner">
    <svg width="480" height="43" viewBox="0 0 480 43"><polygon points="14,0 466,0 480,21.5 466,43 14,43 0,21.5" fill="#f47c20"/></svg>
    <div class="banner__title">FABRICATION &amp; MACHINING CAPABILITIES</div>
  </div>
  <div class="standard">ISO 9001 API TANKS 12F, 620, 650 AWWA</div>

  <div class="grid">
    <div class="cell cell--orange" style="left:12px;top:12px">
      <svg width="32" height="36" viewBox="0 0 32 36"><path d="M6 6h20l4 6-4 6 4 6-4 6H6l-4-6 4-6-4-6z" fill="#fff"/><rect x="4" y="15" width="24" height="6" fill="#e96f34"/></svg>
      <div class="cell__title">HORIZONTAL LEATHERS</div><div class="cell__detail">Up To 24" Dia &amp; 10' Long</div>
    </div>
    <div class="cell" style="left:131px;top:12px">
      <svg width="32" height="36" viewBox="0 0 32 36"><path d="M8 2h16l4 6v20l-4 6H8l-4-6V8z" fill="#fff"/><rect x="14" y="2" width="4" height="32" fill="#2b2b2b"/></svg>
      <div class="cell__title">VERTICLE LEATHERS</div><div class="cell__detail">Up To 44" Dia</div>
    </div>
    <div class="cell cell--orange" style="left:251px;top:12px">
      <svg width="58" height="38" viewBox="0 0 58 38"><rect x="4" y="8" width="32" height="20" rx="3" fill="#fff"/><rect x="36" y="4" width="18" height="6" fill="#fff"/><rect x="46" y="4" width="4" height="20" fill="#fff"/><rect x="0" y="30" width="44" height="6" fill="#fff"/></svg>
      <div class="cell__title">HORIZONTAL BORING<br>MILL CAPABILITIES</div>
    </div>
    <div class="cell" style="left:371px;top:12px;padding-bottom:10px">
      <svg width="32" height="36" viewBox="0 0 32 36"><rect x="12" y="0" width="8" height="10" fill="#fff"/><path d="M6 10l10 10 10-10" stroke="#fff" stroke-width="3" fill="none"/><path d="M2 18l14 8 14-8v18H2z" fill="#fff"/></svg>
      <div class="cell__title">PRESS BRAKE</div><div class="cell__detail">1" Plate x 5' Wide<br>3/8" Plate x 14' Wide</div>
    </div>
    <div class="cell" style="left:12px;top:110px">
      <svg width="30" height="36" viewBox="0 0 30 36"><path d="M6 12a9 9 0 0 1 18 0z" fill="#fff"/><rect x="4" y="12" width="22" height="3" fill="#fff"/><circle cx="15" cy="18" r="5" fill="#fff"/><path d="M2 36v-8a8 8 0 0 1 8-6h10a8 8 0 0 1 8 6v8z" fill="#fff"/></svg>
      <div class="cell__title">IRON WORKERS</div><div class="cell__detail">Up To 85 Tons</div>
    </div>
    <div class="cell cell--orange" style="left:131px;top:110px">
      <svg width="40" height="36" viewBox="0 0 40 36"><polygon points="4,30 30,4 38,10 12,36" fill="#fff"/><rect x="2" y="26" width="10" height="8" fill="#fff" transform="rotate(-45 7 30)"/></svg>
      <div class="cell__title">BAND SAWS</div><div class="cell__detail">22" Cut Capacity</div>
    </div>
    <div class="cell" style="left:251px;top:110px">
      <svg width="56" height="36" viewBox="0 0 56 36"><path d="M18 2L8 30" stroke="#fff" stroke-width="3"/><path d="M22 16h32l-6 10H26z" stroke="#fff" stroke-width="2" fill="none"/><path d="M4 34l4-4" stroke="#f47c20" stroke-width="2"/></svg>
      <div class="cell__title">CNC PLASMA CUTTING</div><div class="cell__detail">8' X 20' Capacity</div>
    </div>
    <div class="cell cell--orange" style="left:371px;top:110px">
      <svg width="56" height="36" viewBox="0 0 56 36"><path d="M38 2l10 28" stroke="#fff" stroke-width="3"/><path d="M2 16h32l-6 10H8z" stroke="#fff" stroke-width="2" fill="none"/></svg>
      <div class="cell__title">CNC ROLL FORMING</div><div class="cell__detail">22" Cut Capacity</div>
    </div>
  </div>

  <div class="services">
    <div class="service" style="left:19px;top:20px"><span class="service__badge">F</span><div><div class="service__title">FACILITY</div><ul class="service__list"><li>35,000 ft2 Facility</li><li>5 Acre Storage Yard</li></ul></div></div>
    <div class="service" style="left:19px;top:64px"><span class="service__badge">✓</span><div><div class="service__title">DESIGN &amp; ENGINEERING</div><ul class="service__list"><li>CAD Drawings</li><li>Engineering Services</li><li>3D Modeling</li></ul></div></div>
    <div class="service" style="left:19px;top:117px"><span class="service__badge">W</span><div><div class="service__title">WELDING PROCESS</div><ul class="service__list"><li>Carbon Steel</li><li>Stainless Steel</li><li>Aluminum</li></ul></div></div>
    <div class="service" style="left:172px;top:17px"><span class="service__badge">H</span><div><div class="service__title">HYDRAULIC ASSEMBLIES</div><ul class="service__list"><li>System Testing</li><li>Hose Assemblies</li><li>Ram Rebuilding</li></ul></div></div>
    <div class="service" style="left:172px;top:73px"><span class="service__badge">D</span><div><div class="service__title">DRIVELINES</div><ul class="service__list"><li>Custom built</li><li>Rebuilding</li><li>Straightening</li></ul></div></div>
    <div class="service" style="left:172px;top:127px"><span class="service__badge">I</span><div><div class="service__title">INSULATING SYSTEMS</div><ul class="service__list"><li>Polyurethane Spray Foam</li><li>Metal Wrap</li><li>Heat Trace</li></ul></div></div>
    <div class="service" style="left:341px;top:15px"><span class="service__badge">P</span><div><div class="service__title">PAINT &amp; CORROSION<br>CONTROL</div><ul class="service__list"><li>Dedicated Paint Bay</li><li>Plural Component Application<br>Equip</li><li>Multi Step Liner Systems</li><li>Stainless Steel Passivation</li><li>Powder Coating</li><li>Galvanizing</li></ul></div></div>
    <div class="service" style="left:341px;top:129px"><span class="service__badge">S</span><div><div class="service__title">SANDBLASTING</div><ul class="service__list"><li>High Production Capacity</li></ul></div></div>
  </div>

  <footer class="footer">
    <div class="contacts">
      <span class="contact"><span class="contact__icon"><svg width="10" height="10" viewBox="0 0 10 10"><path d="M2 1l2 0 1 2-1 1a5 5 0 0 0 2 2l1-1 2 1v2l-1 1C4 9 1 6 1 2z" fill="#e8692a"/></svg></span>555 014 2698</span>
      <span class="contact"><span class="contact__icon"><svg width="10" height="8" viewBox="0 0 10 8"><rect width="10" height="8" rx="1" fill="#e8692a"/><path d="M0 1l5 3.5L10 1" stroke="#fff" fill="none"/></svg></span>office@heronvesselsinc.example</span>
      <span class="contact"><span class="contact__icon"><svg width="11" height="11" viewBox="0 0 11 11"><circle cx="5.5" cy="5.5" r="4.5" stroke="#e8692a" fill="none"/><ellipse cx="5.5" cy="5.5" rx="2" ry="4.5" stroke="#e8692a" fill="none"/><path d="M1 5.5h9" stroke="#e8692a"/></svg></span>www.heronvesselsinc.example</span>
    </div>
    <div class="footer__tab"><svg width="230" height="22" viewBox="0 0 230 22"><polygon points="16,0 214,0 230,22 0,22" fill="#222"/></svg><span>FOR MORE INFORMATION CONTACT US</span></div>
  </footer>
</section>

<!-- BACK -->
<section class="flyer flyer--back">
  <div class="header-photo" role="img" aria-label="Greyscale photo of a tank fabrication yard with pipework and valves"></div>
  <div class="brand"><span class="brand__mark"></span><span class="brand__name">HERON VESSELS, INC.</span></div>
  <div class="banner" style="left:51px;width:400px">
    <svg width="400" height="43" viewBox="0 0 400 43"><polygon points="14,0 386,0 400,21.5 386,43 14,43 0,21.5" fill="#f47c20"/></svg>
    <div class="banner__title">A BRILLIANT IDEA MATERIALIZED</div>
  </div>
  <p class="intro">It is said great ideas start with a brilliant flash. Likewise, we think a brilliant solution starts with an arc. From concept to construction we deliver results for the long haul.</p>

  <div class="panel">
    <div class="sectors">
      <svg width="400" height="25" viewBox="0 0 400 25"><defs><linearGradient id="sectorFill" x1="0" x2="1"><stop offset="0" stop-color="#f47c20"/><stop offset=".5" stop-color="#f08a3e"/><stop offset="1" stop-color="#f47c20"/></linearGradient></defs><polygon points="0,0 400,0 388,25 12,25" fill="url(#sectorFill)"/></svg>
      <ul><li>OIL &amp; GAS</li><li>WATER &amp; WASTE WATER</li><li>POWER GENERATION</li><li>MINING</li></ul>
    </div>
    <div class="offer" style="left:90px;top:45px"><svg width="36" height="36" viewBox="0 0 36 36"><rect x="2" y="10" width="28" height="24" rx="3" fill="#bbb"/><rect x="8" y="2" width="12" height="8" fill="#bbb"/><path d="M31 2c3 5 4 7 4 9a4 4 0 0 1-8 0c0-2 1-4 4-9z" fill="#bbb"/></svg>TANKS</div>
    <div class="offer" style="left:262px;top:45px"><svg width="38" height="36" viewBox="0 0 38 36"><path d="M2 4h14v12h14v16" stroke="#bbb" stroke-width="8" fill="none"/></svg>PIPING</div>
    <div class="offer" style="left:415px;top:45px"><svg width="36" height="36" viewBox="0 0 36 36"><rect x="2" y="8" width="32" height="26" stroke="#bbb" stroke-width="3" fill="none"/><rect x="12" y="4" width="8" height="14" fill="#bbb"/><rect x="24" y="12" width="8" height="8" fill="#bbb"/><rect x="6" y="26" width="24" height="4" fill="#bbb"/></svg>MACHINING</div>
    <div class="offer" style="left:90px;top:124px"><svg width="42" height="36" viewBox="0 0 42 36"><circle cx="21" cy="4" r="3.5" fill="#bbb"/><path d="M21 8l-4 10 6 6M21 12l6 6M19 18l-4 8" stroke="#bbb" stroke-width="3" fill="none"/><rect x="2" y="14" width="38" height="20" rx="2" stroke="#bbb" stroke-width="3" fill="none"/></svg>WALKWAY &amp; STAIRS</div>
    <div class="offer" style="left:262px;top:124px"><svg width="30" height="36" viewBox="0 0 30 36"><ellipse cx="15" cy="5" rx="13" ry="4" fill="#bbb"/><rect x="2" y="10" width="26" height="7" fill="#bbb"/><rect x="2" y="19" width="26" height="7" fill="#bbb"/><rect x="2" y="28" width="26" height="7" rx="3" fill="#bbb"/></svg>TANK LINER SYSTEMS</div>
    <div class="offer" style="left:415px;top:124px"><svg width="36" height="36" viewBox="0 0 36 36"><circle cx="15" cy="14" r="12" stroke="#bbb" stroke-width="3" fill="none"/><circle cx="15" cy="14" r="6" stroke="#bbb" stroke-width="3" fill="none"/><rect x="2" y="28" width="32" height="6" stroke="#bbb" stroke-width="2" fill="none"/></svg>INSULATION</div>
  </div>

  <div class="gallery">
    <div class="photo photo--welder" role="img" aria-label="Photo of a welder in a helmet grinding metal with sparks flying"></div>
    <div class="photo photo--fittings" role="img" aria-label="Photo of assorted stainless steel pipe fittings"></div>
    <div class="photo photo--pipes" role="img" aria-label="Close-up photo of welded stainless steel pipe bends with flanges"></div>
  </div>

  <footer class="footer">
    <div class="contacts">
      <span class="contact"><span class="contact__icon"><svg width="10" height="10" viewBox="0 0 10 10"><path d="M2 1l2 0 1 2-1 1a5 5 0 0 0 2 2l1-1 2 1v2l-1 1C4 9 1 6 1 2z" fill="#e8692a"/></svg></span>555 014 2698</span>
      <span class="contact"><span class="contact__icon"><svg width="10" height="8" viewBox="0 0 10 8"><rect width="10" height="8" rx="1" fill="#e8692a"/><path d="M0 1l5 3.5L10 1" stroke="#fff" fill="none"/></svg></span>office@heronvesselsinc.example</span>
      <span class="contact"><span class="contact__icon"><svg width="11" height="11" viewBox="0 0 11 11"><circle cx="5.5" cy="5.5" r="4.5" stroke="#e8692a" fill="none"/><ellipse cx="5.5" cy="5.5" rx="2" ry="4.5" stroke="#e8692a" fill="none"/><path d="M1 5.5h9" stroke="#e8692a"/></svg></span>www.heronvesselsinc.example</span>
    </div>
    <div class="footer__tab"><svg width="230" height="22" viewBox="0 0 230 22"><polygon points="16,0 214,0 230,22 0,22" fill="#222"/></svg><span>FOR MORE INFORMATION CONTACT US</span></div>
  </footer>
</section>

</body>
</html>
```